Sleek wordpress site for Bramblecrest finishing works

We are a commercial job shop that serves B2B, govt & LEO and retail clients.We need a wordpress site with 6 individual pages: homepage, coating, laser engraving, laser cutting, part marking, and contact us. I have attached an outline of the desired flow and sub headings for each page. I would like to incorporate the colors of the logo through out the site to be clean and sleek enough to appeal to B2B commercial clients yet be inviting enough for retail clients.

I would like to have easy picture functionality so photographs on each page can be updated easily.

Target Market(s)

B2B industrial & Govt and Military part marking, laser engraving and coating: machine shops, aerospace companies, tool manufactures. Retail: personalized gifts, Job Shop

Coding

Coded - Design and coding required

Font styles to use
Sans Serif
Other font styles liked:
• Open to suggestion

Colors
0255a3
3176b5
eaf1f7
cfdeed
ffffff

Requirements
Must have
• Clean easy to navigate flow, separate pages as indicated on attached outline, high class feel. Great picture functionality, professional and inviting feel,
• **update: needs to be optimized for mobile, should have a gallery function. Gallery can be an additional page or embedded
Nice to have
• Social media connectivity links,
Should not have
• crappy plugins that make back-end management difficult, no blog

```html
<!DOCTYPE html>
<html lang="en">
<head>
<meta charset="utf-8">
<title>Bramblecrest Finishing Works</title>
<link href="https://fonts.googleapis.com/css2?family=Montserrat:wght@500;600;700;800&family=Poppins:wght@600&family=Roboto:wght@400;500&display=swap" rel="stylesheet">
<style>
:root{
  --blue:#0255a3;
  --blue-mid:#3176b5;
  --blue-pale:#eaf1f7;
  --blue-soft:#cfdeed;
  --white:#ffffff;
  --ink:#1c1c1c;
  --text:#333333;
  --warm-gray:#f4f0f0;
  --footer:#0b4aa2;
}
*{margin:0;padding:0;box-sizing:border-box}
html,body{width:1200px;height:2651px;overflow:hidden;background:var(--white)}
body{position:relative;font-family:'Roboto',sans-serif;color:var(--text)}
.abs{position:absolute}

/* header */
.site-header{position:absolute;left:0;top:0;width:1200px;height:145px;background:var(--white)}
.brand{position:absolute;left:128px;top:48px;display:flex;align-items:center;gap:10px;font-family:'Montserrat',sans-serif;font-weight:800;font-size:17px;color:var(--blue);line-height:1.15;text-transform:uppercase;width:240px}
.brand-dot{width:38px;height:38px;border-radius:50%;background:var(--blue);flex:none}
.call{position:absolute;left:790px;top:32px;display:flex;gap:12px;align-items:center}
.call small{display:block;font-family:'Montserrat',sans-serif;font-size:12px;font-weight:600;color:var(--ink)}
.call strong{display:block;font-family:'Montserrat',sans-serif;font-size:19px;font-weight:700;color:var(--blue)}
.follow{position:absolute;left:986px;top:32px;font-family:'Montserrat',sans-serif;font-size:12px;font-weight:600;color:var(--ink)}
.follow .sq{display:flex;gap:8px;margin-top:8px}
.follow .sq span{width:20px;height:20px;background:var(--blue)}
.follow .sq span:nth-child(2){background:#1da1f2}
.main-nav{position:absolute;top:102px;left:388px;display:flex;align-items:center;font-family:'Montserrat',sans-serif;font-size:12.5px;font-weight:600;color:var(--ink)}
.main-nav a{color:inherit;text-decoration:none;padding:7px 11px;margin-right:27px}
.main-nav a.active{background:var(--blue);color:var(--white);margin-right:26px}
.main-nav a:last-child{margin-right:0}

/* hero */
.hero{position:absolute;left:0;top:145px;width:1200px;height:593px;background:linear-gradient(180deg,#6a6a6a 0%,#8a8a88 45%,#bdbdbb 75%,#9e9e9c 100%)}
.hero-title{position:absolute;left:652px;top:128px;font-family:'Montserrat',sans-serif;font-weight:800;font-size:34px;line-height:42px;color:var(--white);text-transform:uppercase}
.btn{display:inline-block;background:var(--blue);color:var(--white);font-family:'Montserrat',sans-serif;font-weight:700;text-transform:uppercase;text-decoration:none}
.hero .btn{position:absolute;left:654px;top:225px;width:151px;height:46px;line-height:46px;text-align:center;font-size:15px}
.dots{position:absolute;top:524px;left:540px;display:flex;gap:14px;align-items:center}
.dots span{width:9px;height:9px;border-radius:50%;background:var(--white)}
.dots span.on{width:15px;height:15px;background:transparent;border:2px solid var(--white)}

/* services */
.services{position:absolute;left:0;top:738px;width:1200px;height:542px;display:flex;gap:4px;background:#e6e6e6}
.service{flex:1;position:relative;background:var(--white)}
.service .photo{height:423px}
.service .icon{position:absolute;left:50%;top:377px;width:92px;height:92px;margin-left:-46px;border-radius:50%;background:var(--white);display:flex;align-items:center;justify-content:center}
.service h3{position:absolute;top:465px;width:100%;text-align:center;font-family:'Poppins',sans-serif;font-weight:600;font-size:24px;color:var(--ink)}

/* welcome */
.welcome{position:absolute;left:0;top:1280px;width:1200px;height:532px}
.welcome-copy{position:absolute;left:0;top:0;width:600px;height:532px;background:var(--warm-gray)}
.welcome-copy .kicker{position:absolute;left:165px;top:100px;font-family:'Montserrat',sans-serif;font-weight:600;font-size:15px;color:var(--ink)}
.welcome-copy h2{position:absolute;left:165px;top:131px;font-family:'Montserrat',sans-serif;font-weight:800;font-size:26px;line-height:32px;color:var(--blue);text-transform:uppercase}
.welcome-copy p{position:absolute;left:165px;top:226px;width:350px;font-size:13.5px;line-height:18px;color:var(--text)}
.welcome-copy .btn{position:absolute;left:165px;top:377px;width:122px;height:36px;line-height:36px;text-align:center;font-size:13px}
.welcome-photo{position:absolute;left:600px;top:0;width:600px;height:532px;background:linear-gradient(180deg,#bcd4ea 0%,#d9e4ec 35%,#8f8a82 60%,#a9a39a 80%,#6e8f58 100%)}

/* testimonials */
.testimonials{position:absolute;left:0;top:1812px;width:1200px;height:458px;text-align:center}
.testimonials h2{position:absolute;top:78px;width:100%;font-family:'Montserrat',sans-serif;font-weight:800;font-size:25px;color:var(--blue)}
.rule{position:absolute;top:128px;left:580px;width:40px;height:4px;background:#9a9a9a}
.quote-mark{position:absolute;left:345px;top:140px;font-family:'Montserrat',sans-serif;font-weight:800;font-size:70px;color:var(--blue);line-height:1}
.testimonials blockquote{position:absolute;left:380px;top:186px;width:450px;font-size:15.5px;line-height:20px;color:var(--text)}
.arrow{position:absolute;top:228px;width:36px;height:36px;border:1.5px solid #9a9a9a;border-radius:50%}
.arrow svg{position:absolute;left:11px;top:10px}
.author{position:absolute;left:540px;top:338px;display:flex;align-items:center;gap:14px;text-align:left}
.avatar{width:42px;height:42px;border-radius:50%;background:#8a7366}
.author b{display:block;font-family:'Montserrat',sans-serif;font-size:11px;font-weight:700;color:var(--ink)}
.author span{font-size:11px;color:var(--text)}

/* footer */
.site-footer{position:absolute;left:0;top:2270px;width:1200px;height:381px;background:var(--footer);color:var(--white)}
.footer-brand{position:absolute;left:130px;top:75px;display:flex;align-items:center;gap:12px;font-family:'Montserrat',sans-serif;font-weight:800;font-size:20px;line-height:1.2;text-transform:uppercase;width:260px}
.footer-brand .brand-dot{background:var(--white);width:44px;height:44px}
.footer-col{position:absolute;top:62px;font-size:11.5px}
.footer-col h4{font-family:'Montserrat',sans-serif;font-weight:700;font-size:12px;margin-bottom:22px}
.contact-col{left:475px}
.contact-col li{list-style:none;display:flex;gap:12px;margin-bottom:16px;line-height:17px}
.menu-col{left:733px}
.menu-col li{list-style:none;line-height:17.5px}
.social-col{left:936px}
.social-col li{list-style:none;display:flex;align-items:center;gap:12px;margin-bottom:16px}
.social-col li i{width:24px;height:24px;border-radius:50%;background:#15357a;display:block}
.footer-line{position:absolute;left:130px;top:276px;width:940px;height:1px;background:rgba(255,255,255,.25)}
.copyright{position:absolute;top:322px;width:100%;text-align:center;font-size:11.5px}
</style>
</head>
<body>

<header class="site-header">
  <div class="brand"><span class="brand-dot"></span>Bramblecrest Finishing Works</div>
  <div class="call">
    <svg width="30" height="30" viewBox="0 0 24 24" fill="none" stroke="#0255a3" stroke-width="1.6"><path d="M5 3h4l2 5-2.5 1.5a11 11 0 0 0 6 6L16 13l5 2v4a2 2 0 0 1-2 2A16 16 0 0 1 3 5a2 2 0 0 1 2-2z"/></svg>
    <div><small>Call us Now on</small><strong>555.014.2290</strong></div>
  </div>
  <div class="follow">Follow us on<div class="sq"><span></span><span></span><span></span></div></div>
  <nav class="main-nav">
    <a class="active" href="#">HOME</a><a href="#">COATING</a><a href="#">LASER ENGRAVING</a><a href="#">LASER CUTTING</a><a href="#">PART MARKING</a><a href="#">CONTACT US.</a>
  </nav>
</header>

<section class="hero" role="img" aria-label="Close-up of an engraving spindle cutting lettering into a metal plate">
  <h1 class="hero-title">Bramblecrest<br>Finishing Works</h1>
  <a class="btn" href="#">Read More</a>
  <div class="dots"><span></span><span></span><span class="on"></span><span></span><span></span></div>
</section>

<section class="services">
  <article class="service">
    <div class="photo" role="img" aria-label="Engraving machine head over a metal part" style="background:linear-gradient(180deg,#7b7b7b,#b5b5b3 60%,#8d8d8b)"></div>
    <div class="icon"><svg width="54" height="54" viewBox="0 0 54 54" fill="none" stroke="#0255a3" stroke-width="2.5"><path d="M12 8h30l-8 14H20z"/><path d="M27 22v14"/><path d="M8 46h38"/></svg></div>
    <h3>Laser Engraving</h3>
  </article>
  <article class="service">
    <div class="photo" role="img" aria-label="Laser cutting nozzle throwing sparks across sheet metal" style="background:linear-gradient(180deg,#4b4a48,#7a6a52 55%,#c98a3a 72%,#5a5855)"></div>
    <div class="icon"><svg width="54" height="54" viewBox="0 0 54 54" fill="none" stroke="#0255a3" stroke-width="2.5"><path d="M16 8h22v10H16z"/><path d="M21 18l6 14 6-14"/><path d="M8 46h38"/></svg></div>
    <h3>Laser Cutting</h3>
  </article>
  <article class="service">
    <div class="photo" role="img" aria-label="Metal cylinder with stamped serial part markings" style="background:linear-gradient(180deg,#5e5e5e,#a8a8a6 40%,#6d6d6b 70%,#9a9a98)"></div>
    <div class="icon"><svg width="54" height="54" viewBox="0 0 54 54" fill="none" stroke="#0255a3" stroke-width="3"><path d="M12 42L38 16"/><path d="M34 12l8 8"/><path d="M12 34l8 8"/></svg></div>
    <h3>Part Marking</h3>
  </article>
  <article class="service">
    <div class="photo" role="img" aria-label="Spray gun applying an orange coating in a booth" style="background:linear-gradient(180deg,#8a8f96,#c9a489 45%,#e8813a 70%,#8d8a86)"></div>
    <div class="icon"><svg width="54" height="54" viewBox="0 0 54 54" fill="none" stroke="#0255a3" stroke-width="2.5"><path d="M22 14h20v12H22z"/><path d="M30 26v16h6V26"/><path d="M22 20H12"/><circle cx="8" cy="16" r="1.5"/><circle cx="8" cy="24" r="1.5"/></svg></div>
    <h3>Coatings</h3>
  </article>
</section>

<section class="welcome">
  <div class="welcome-copy">
    <p class="kicker">WELCOME TO</p>
    <h2>Bramblecrest<br>Finishing Works</h2>
    <p>Sed ut perspiciatis unde omnis iste natus error sit voluptatem accusantium doloremque laudantium, totam rem aperiam, eaque ipsa quae ab illo inventore veritatis et quasi architecto beatae vitae dicta sunt explicabo. Nemo enim ipsam voluptatem quia voluptas sit aspernatur aut odit aut fugit.</p>
    <a class="btn" href="#">Read More</a>
  </div>
  <div class="welcome-photo" role="img" aria-label="Exterior of the company storefront building with trees and lawn"></div>
</section>

<section class="testimonials">
  <h2>TESTIMONIALS</h2>
  <div class="rule"></div>
  <div class="quote-mark">&ldquo;</div>
  <blockquote>Sed ut perspiciatis unde omnis iste natus error sit voluptatem accusantium doloremque laudantium, totam rem aperiam, eaque ipsa quae ab illo inventore veritatis et quasi architecto beatae vitae dicta sunt explicabo. Nemo enim ipsam voluptatem quia voluptas sit aspernatur aut odit aut fugit.</blockquote>
  <span class="arrow" style="left:133px"><svg width="12" height="14" viewBox="0 0 12 14" fill="none" stroke="#777" stroke-width="1.6"><path d="M8 2L3 7l5 5"/></svg></span>
  <span class="arrow" style="left:1034px"><svg width="12" height="14" viewBox="0 0 12 14" fill="none" stroke="#777" stroke-width="1.6"><path d="M4 2l5 5-5 5"/></svg></span>
  <div class="author"><div class="avatar" role="img" aria-label="Client portrait"></div><div><b>EDWIN</b><span>England</span></div></div>
</section>

<footer class="site-footer">
  <div class="footer-brand"><span class="brand-dot"></span>Bramblecrest Finishing Works</div>
  <div class="footer-col contact-col">
    <h4>CONTACT US</h4>
    <ul>
      <li><svg width="10" height="14" viewBox="0 0 10 14" fill="#fff"><path d="M5 0a5 5 0 0 1 5 5c0 4-5 9-5 9S0 9 0 5a5 5 0 0 1 5-5z"/></svg><span>18 Foundry Lane #4<br>Tarnwick, OR 97000</span></li>
      <li><svg width="11" height="11" viewBox="0 0 24 24" fill="#fff"><path d="M5 3h4l2 5-2.5 1.5a11 11 0 0 0 6 6L16 13l5 2v4a2 2 0 0 1-2 2A16 16 0 0 1 3 5a2 2 0 0 1 2-2z"/></svg><span>555.014.2290</span></li>
      <li><svg width="12" height="10" viewBox="0 0 12 10" fill="#fff"><path d="M0 0h12v10H0z"/><path d="M0 0l6 5 6-5" stroke="#0b4aa2" fill="none"/></svg><span>hello@bramblecrestworks.com</span></li>
    </ul>
  </div>
  <div class="footer-col menu-col">
    <h4>MENU</h4>
    <ul><li>Home</li><li>Coating</li><li>Laser engraving</li><li>Laser cutting</li><li>Part marking</li><li>Contact us.</li></ul>
  </div>
  <div class="footer-col social-col">
    <h4>CONNECT WITH US</h4>
    <ul><li><i></i>Friendsquare</li><li><i></i>Chirpline</li><li><i></i>Worknet</li></ul>
  </div>
  <div class="footer-line"></div>
  <p class="copyright">Copyrights @ 2018 All Rights Reserved</p>
</footer>

</body>
</html>
```